Alberta, Canada based Environmental Oilfield Consultant need a Business Card Design

We need a business card design for a year old company based in Edmonton, Alberta, Canada called Cindermoor Consulting Inc. We are environmental consultants primarily for oilfield based companies (pipeline cleanup, site consultations, environmental site training, and site evaluations).

We like the color blue or green, something very clean and crisp looking.
We don't really care if there is an otter on it but most of our work is land based and nothing really to do with oceans or larger bodies of water.

The name Cindermoor was the name of our fathers boat, and named our company that in his memory.

```html
<!DOCTYPE html>
<html lang="en">
<head>
<meta charset="utf-8">
<title>Cindermoor Consulting Inc. – Business Card</title>
<link rel="stylesheet" href="https://fonts.googleapis.com/css2?family=Archivo+Black&family=Michroma&display=swap">
<style>
  :root {
    --bg: #ececec;
    --yellow-hot: #ffe21c;
    --yellow: #ffc414;
    --orange: #f5a000;
    --gold-dark: #b88a08;
    --gold-light: #e8c21c;
    --frame-grey: #8c8c8c;
    --panel-grey: #9a9a9a;
    --panel-grey-light: #d2d2d2;
    --ink: #3a3a3a;
    --ink-soft: #2c2c2c;
    --white: #ffffff;
  }
  * { box-sizing: border-box; margin: 0; padding: 0; }
  html, body { width: 1200px; height: 786px; overflow: hidden; }
  body {
    background: var(--bg);
    position: relative;
    font-family: "Michroma", sans-serif;
  }
  .card {
    position: absolute;
    top: 240px;
    width: 530px;
    height: 303px;
    box-shadow: 0 6px 18px rgba(0,0,0,0.18);
  }
  /* Front */
  .card-front {
    left: 50px;
    background: var(--frame-grey);
    padding: 14px;
  }
  .card-front .face {
    width: 100%;
    height: 100%;
    background: radial-gradient(ellipse at 45% 40%, var(--yellow-hot) 0%, var(--yellow) 45%, var(--orange) 100%);
    position: relative;
  }
  .wordmark {
    font-family: "Archivo Black", sans-serif;
    color: var(--ink);
    line-height: 0.95;
    letter-spacing: -0.5px;
  }
  .card-front .wordmark {
    position: absolute;
    left: 110px;
    top: 78px;
    font-size: 44px;
  }
  .card-front .wordmark .line-2 { padding-left: 0; }

  /* Back */
  .card-back {
    left: 620px;
    background: var(--orange);
    padding: 12px;
  }
  .card-back .face {
    width: 100%;
    height: 100%;
    background: var(--white);
    position: relative;
    overflow: hidden;
  }
  .card-back .wordmark {
    position: absolute;
    left: 40px;
    top: 14px;
    font-size: 33px;
  }
  .column { position: absolute; bottom: 0; }
  .col-phone { left: 0; width: 176px; top: 80px; }
  .col-web { left: 176px; width: 156px; top: 130px; }
  .col-address { left: 332px; width: 174px; top: 192px; }

  .col-header {
    height: 32px;
    display: flex;
    align-items: center;
    justify-content: center;
  }
  .col-phone .col-header,
  .col-address .col-header {
    background: linear-gradient(90deg, var(--gold-dark), var(--gold-light) 55%, var(--gold-dark));
  }
  .col-web .col-header {
    background: linear-gradient(90deg, #7a7a7a, var(--panel-grey) 50%, #7a7a7a);
    height: 36px;
  }
  .col-body {
    position: absolute;
    top: 32px; left: 0; right: 0; bottom: 0;
    padding: 16px 14px;
    font-size: 9px;
    line-height: 1.7;
    color: var(--ink-soft);
  }
  .col-phone .col-body,
  .col-address .col-body {
    background: radial-gradient(ellipse at 50% 40%, var(--yellow-hot), var(--yellow) 60%, var(--orange));
  }
  .col-web .col-body {
    top: 36px;
    background: radial-gradient(ellipse at 50% 40%, #f2f2f2, var(--panel-grey-light) 55%, var(--panel-grey));
    font-size: 8px;
    padding-top: 22px;
  }
  .col-phone .col-body { padding-top: 28px; padding-left: 22px; }
  .col-address .col-body { font-size: 8px; padding-top: 12px; }

  .icon { width: 20px; height: 20px; display: block; }

  .person {
    position: absolute;
    right: 16px;
    top: 146px;
    text-align: right;
    color: var(--ink-soft);
  }
  .person-name { font-size: 12px; letter-spacing: 0.5px; }
  .person-role { font-size: 9px; margin-top: 2px; }
</style>
</head>
<body>
  <section class="card card-front" aria-label="Business card front">
    <div class="face">
      <div class="wordmark">
        <div class="line-1">Cindermoor</div>
        <div class="line-2">Consulting</div>
      </div>
    </div>
  </section>

  <section class="card card-back" aria-label="Business card back">
    <div class="face">
      <div class="wordmark">
        <div>Cindermoor</div>
        <div>Consulting</div>
      </div>

      <div class="column col-phone">
        <div class="col-header">
          <svg class="icon" viewBox="0 0 20 20" aria-hidden="true">
            <circle cx="10" cy="10" r="8.5" fill="none" stroke="#2c2c2c" stroke-width="1.4"/>
            <path d="M7.3 5.6c.5-.3 1-.2 1.2.3l.7 1.5c.2.4 0 .8-.3 1l-.6.4c.4 1 1.2 1.9 2.2 2.5l.5-.6c.3-.3.7-.4 1-.2l1.5.8c.4.2.5.7.3 1.1-.6 1.1-1.7 1.5-2.8 1-2.2-1-3.9-2.8-4.6-5-.3-1.1.1-2.2.9-2.8z" fill="#2c2c2c"/>
          </svg>
        </div>
        <div class="col-body">
          <div>012 555 0147</div>
          <div>012 555 0148</div>
        </div>
      </div>

      <div class="column col-web">
        <div class="col-header">
          <svg class="icon" viewBox="0 0 20 20" aria-hidden="true">
            <circle cx="10" cy="10" r="8" fill="none" stroke="#fff" stroke-width="1.3"/>
            <ellipse cx="10" cy="10" rx="3.5" ry="8" fill="none" stroke="#fff" stroke-width="1.1"/>
            <line x1="2" y1="10" x2="18" y2="10" stroke="#fff" stroke-width="1.1"/>
            <line x1="3.5" y1="6" x2="16.5" y2="6" stroke="#fff" stroke-width="1"/>
            <line x1="3.5" y1="14" x2="16.5" y2="14" stroke="#fff" stroke-width="1"/>
          </svg>
        </div>
        <div class="col-body">
          <div>info@cindermoor.ca</div>
          <div>www.cindermoorconsult.ca</div>
        </div>
      </div>

      <div class="person">
        <div class="person-name">ALAN REEVE</div>
        <div class="person-role">GENERAL MANAGER</div>
      </div>

      <div class="column col-address">
        <div class="col-header">
          <svg class="icon" viewBox="0 0 20 20" aria-hidden="true">
            <circle cx="10" cy="10" r="8.5" fill="none" stroke="#2c2c2c" stroke-width="1.4"/>
            <path d="M10 4.5a3.4 3.4 0 0 0-3.4 3.4c0 2.5 3.4 6.4 3.4 6.4s3.4-3.9 3.4-6.4A3.4 3.4 0 0 0 10 4.5z" fill="#2c2c2c"/>
            <circle cx="10" cy="7.9" r="1.2" fill="#e8c21c"/>
          </svg>
        </div>
        <div class="col-body">
          <div>214 Birchwood Ave, Unit 5</div>
          <div>Edmonton AB</div>
        </div>
      </div>
    </div>
  </section>
</body>
</html>
```